Carrying bags for customer visit

I am looking to make a carrying case that can be used to carry small presents, gifts, our brochure (20 inch X20 inch) and sometimes our samples (which are printed circuit boards that have a size of 24X15). The case should look elegant, show our company logo and our slogan "PCB is our business". You can try to download our logo from our web site www.tvolamiq.com. I want a contemporary and cool feel of the carrying case that can be any materials. I prefer to use recyclable materials that reflects our company's business philosophy of practicing sustanbility. Also I would like to add Chinese name “泓岚科技(东莞)有限公司" in the bag.

Target Market(s)

Corporate customers who will come into contact with our companies

Colors

Designer to choose colors to be used in the design.

Requirements
Must have
• It has to be attractive and people wanting to use them on a regular basis. Therefore, the logo display and our slogan should be subtle. I want the carrying bags not to be very expensive to produce.

```html
<!DOCTYPE html>
<html lang="zh">
<head>
<meta charset="utf-8">
<title>泓岚科技 Carrying Bag – Front Panel</title>
<link rel="stylesheet" href="https://fonts.googleapis.com/css2?family=Noto+Sans+SC:wght@400;700&family=Oswald:wght@400&display=swap">
<style>
  :root {
    --panel-grey: #d9d9d9;
    --teal-brand: #0f6b66;
    --teal-glow: #13a09e;
    --teal-mid: #137a78;
    --teal-deep: #1b373b;
    --text-grey: #4a4a4a;
  }
  * { margin: 0; padding: 0; box-sizing: border-box; }
  html, body { width: 1200px; height: 1200px; overflow: hidden; background: #ffffff; }
  .bag-front {
    position: relative;
    width: 1200px;
    height: 1200px;
    background: var(--panel-grey);
    overflow: hidden;
  }
  .handle-tab {
    position: absolute;
    left: 484px;
    top: 0;
    width: 250px;
    height: 175px;
    background: linear-gradient(180deg, #0d5553 0%, var(--teal-glow) 55%, #0b4a4a 100%);
  }
  .brand-block {
    position: absolute;
    left: 0;
    right: 0;
    top: 196px;
    text-align: center;
  }
  .brand-name {
    display: inline-block;
    font-family: "Noto Sans SC", sans-serif;
    font-weight: 700;
    font-size: 62px;
    line-height: 1;
    letter-spacing: 4px;
    color: var(--teal-brand);
    padding-bottom: 8px;
    border-bottom: 2px solid var(--teal-brand);
  }
  .slogan {
    margin-top: 8px;
    font-family: "Oswald", sans-serif;
    font-size: 15px;
    letter-spacing: 1.6px;
    color: var(--text-grey);
  }
  .company-cn {
    margin-top: 18px;
    font-family: "Noto Sans SC", sans-serif;
    font-weight: 400;
    font-size: 40px;
    letter-spacing: 2px;
    color: var(--teal-brand);
  }
  .lower-panel {
    position: absolute;
    left: 0;
    top: 407px;
    width: 1200px;
    height: 793px;
    background: radial-gradient(ellipse 620px 520px at 56% 22%, var(--teal-glow) 0%, var(--teal-mid) 35%, #17504f 70%, var(--teal-deep) 100%);
  }
  .circuit-art {
    position: absolute;
    left: 0;
    top: 0;
    width: 520px;
    height: 650px;
    background: radial-gradient(ellipse 300px 360px at 45% 35%, rgba(40, 200, 195, 0.28) 0%, rgba(40, 200, 195, 0.1) 60%, rgba(40, 200, 195, 0) 100%);
  }
</style>
</head>
<body>
  <main class="bag-front">
    <div class="handle-tab"></div>
    <header class="brand-block">
      <div class="brand-name">TVOLAMIQ</div>
      <p class="slogan">Printed Circuit Boards Is Our Business</p>
      <p class="company-cn">泓岚科技（东莞）有限公司</p>
    </header>
    <section class="lower-panel">
      <div class="circuit-art" role="img" aria-label="Glowing circuit board traces branching downward with pads and nodes"></div>
    </section>
  </main>
</body>
</html>
```